Lawn sign for construction company

Would like this to be a very clean and high end design for luxury homes. We need a yard sign designed that includes the company logo, website, phone number and major service offerings (residential and commercial renovations and maintenance)
The company website is brackwellbuilders.com all other contact info is in the attachments
Target Market(s)
Luxury home owners and business owners
Industry/Entity Type
Construction/Home Improvement
Font styles to use
Other font styles liked:
- See company logo and other graphics included for title text fonts. All other fonts can be standard sans serif.
Colors
0054AA
0677BA
7BADD7
CADEEF
E8F1F8
Requirements
Must have
- Clean, easy to read design, would like 2 sided sign. A main sign side and back side which states “free estimates, and includes the website and phone number. Must also match the color scheme of the provided logo and other company images. Dark Navy blue primary color, gray secondary color, and orange as an accent color.
Nice to have
- 2nd sign side very simple design
Should not have
- Too many graphics limit to 1-3 colors

```html
<!DOCTYPE html>
<html lang="en">
<head>
<meta charset="utf-8">
<title>Brackwell Builders – Lawn Sign</title>
<link href="https://fonts.googleapis.com/css2?family=Barlow+Condensed:wght@600;700&family=Poppins:wght@800&family=Open+Sans:wght@700&display=swap" rel="stylesheet">
<style>
:root{
  --navy:#1c2652;
  --navy-deep:#161f45;
  --orange:#f28705;
  --grey:#6b6b6b;
  --white:#ffffff;
  --stage:#8dbfc4;
  --ink:#1d1d1d;
}
*{box-sizing:border-box;margin:0;padding:0}
html,body{width:1006px;height:1200px;overflow:hidden}
body{background:var(--stage);font-family:"Poppins",sans-serif;display:flex;flex-direction:column;align-items:center;padding-top:14px}
.side-label{font-family:"Open Sans",sans-serif;font-weight:700;font-size:40px;color:var(--ink);letter-spacing:1px;height:46px;line-height:46px;margin-bottom:8px}
.sign{position:relative;width:700px;height:524px;box-shadow:0 6px 14px rgba(0,0,0,.28);overflow:hidden}
.sign + .side-label{margin-top:18px}

/* front */
.front{background:var(--navy)}
.front .top{position:absolute;left:0;top:0;width:100%;height:190px;background:linear-gradient(135deg,#f3f3f3 0%,#ffffff 40%,#f4f4f4 100%)}
.front .sheen{position:absolute;left:0;top:190px;width:100%;height:265px;background:linear-gradient(135deg,rgba(255,255,255,.05) 0%,rgba(255,255,255,0) 45%,rgba(0,0,0,.08) 100%)}
.brand{position:absolute;left:0;right:0;top:210px;display:flex;align-items:center;justify-content:center;gap:16px}
.brand-dot{width:46px;height:46px;border-radius:50%;background:var(--grey)}
.brand-name{font-family:"Barlow Condensed",sans-serif;font-weight:700;font-size:64px;color:var(--orange);letter-spacing:1px;line-height:1}
.front .top .brand{top:62px}
.headline{position:absolute;left:0;right:0;top:340px;text-align:center;color:var(--white);font-weight:800;font-size:34px;line-height:46px;letter-spacing:.3px}
.headline .accent{color:var(--orange)}
.services{position:absolute;left:0;top:455px;width:100%;height:46px;background:var(--orange);display:flex;align-items:center;justify-content:center}
.service{display:flex;align-items:center;gap:6px;font-family:"Barlow Condensed",sans-serif;font-weight:600;font-size:22px;color:var(--white);padding:0 14px}
.service + .service{border-left:1px solid rgba(255,255,255,.55)}
.service svg{width:18px;height:18px}

/* back */
.back{background:var(--navy-deep)}
.icon-ring{position:absolute;left:50%;transform:translateX(-50%);width:70px;height:70px;border-radius:50%;border:3px solid var(--orange);background:var(--navy-deep);display:flex;align-items:center;justify-content:center}
.icon-ring .core{width:54px;height:54px;border-radius:50%;background:var(--navy);display:flex;align-items:center;justify-content:center}
.icon-ring svg{width:30px;height:30px}
.phone-ring{top:80px}
.phone-box{position:absolute;left:65px;width:570px;top:166px;height:112px;background:var(--orange);border-radius:10px;display:flex;align-items:center;justify-content:center;font-family:"Barlow Condensed",sans-serif;font-weight:700;font-size:96px;color:var(--white);letter-spacing:1px}
.web-box{position:absolute;left:32px;width:636px;top:322px;height:114px;border:2px solid var(--orange);border-radius:6px;display:flex;align-items:flex-end;justify-content:center;padding-bottom:12px;font-family:"Barlow Condensed",sans-serif;font-weight:700;font-size:64px;color:var(--white)}
.web-ring{top:285px}
</style>
</head>
<body>

<div class="side-label">FRONT</div>
<section class="sign front" aria-label="Sign front side">
  <div class="top">
    <div class="brand">
      <span class="brand-dot"></span>
      <span class="brand-name">BRACKWELL BUILDERS</span>
    </div>
  </div>
  <div class="sheen"></div>
  <h1 class="headline">RESIDENTIAL <span class="accent">AND</span> COMMERCIAL<br>RENOVATIONS <span class="accent">AND</span> MAINTENANCE</h1>
  <ul class="services">
    <li class="service"><svg viewBox="0 0 20 20" fill="none" stroke="#fff" stroke-width="1.8"><circle cx="10" cy="10" r="8"/><path d="M6 10l3 3 6-7"/></svg>GENERAL CONTRACTING</li>
    <li class="service"><svg viewBox="0 0 20 20" fill="none" stroke="#fff" stroke-width="1.8"><circle cx="10" cy="10" r="8"/><path d="M6 10l3 3 6-7"/></svg>PROPERTY MANAGEMENT</li>
    <li class="service"><svg viewBox="0 0 20 20" fill="none" stroke="#fff" stroke-width="1.8"><circle cx="10" cy="10" r="8"/><path d="M6 10l3 3 6-7"/></svg>REMODELING</li>
  </ul>
</section>

<div class="side-label">BACK</div>
<section class="sign back" aria-label="Sign back side">
  <div class="icon-ring phone-ring"><div class="core">
    <svg viewBox="0 0 24 24" fill="#fff"><path d="M6.6 10.8a15.1 15.1 0 0 0 6.6 6.6l2.2-2.2a1 1 0 0 1 1-.25 11.4 11.4 0 0 0 3.6.57 1 1 0 0 1 1 1V20a1 1 0 0 1-1 1A17 17 0 0 1 3 4a1 1 0 0 1 1-1h3.5a1 1 0 0 1 1 1c0 1.25.2 2.45.57 3.57a1 1 0 0 1-.25 1z"/></svg>
  </div></div>
  <div class="phone-box">810.555.0147</div>
  <div class="web-box">brackwellbuilders.com</div>
  <div class="icon-ring web-ring"><div class="core">
    <svg viewBox="0 0 24 24" fill="none" stroke="#fff" stroke-width="1.8"><circle cx="12" cy="12" r="9"/><path d="M3 12h18M12 3c3 3 3 15 0 18M12 3c-3 3-3 15 0 18"/></svg>
  </div></div>
</section>

</body>
</html>
```